Northfield Builders Guild Business card

We are looking for a new business card design with photo included.
Our business is a nonprofit construction contractor membership organization. We offer business education, assist with business setup and licensing, provide safety training, and provide a member directory.
URL: www.builderslinkguild.org
Color code:
CMYK: 0 cyan, 42 magenta, 100 yellow, 0 black for Print.
Hexidecimal: #FF9900
RGB: R 255; G 153; B 0

```html
<!DOCTYPE html>
<html lang="en">
<head>
<meta charset="utf-8">
<title>Northfield Builders Guild – Business Card</title>
<link href="https://fonts.googleapis.com/css2?family=Jost:wght@400;500;700;800&display=swap" rel="stylesheet">
<style>
  :root{
    --orange:#FF9900;
    --charcoal:#353334;
    --ink:#3a3a3a;
    --paper:#ffffff;
    --backdrop:#e4e4e4;
  }
  *{margin:0;padding:0;box-sizing:border-box}
  html,body{width:1200px;height:1200px;overflow:hidden}
  body{background:var(--backdrop);font-family:"Jost",sans-serif;position:relative}
  .card{position:absolute;left:262px;width:686px;height:392px;border-radius:20px;overflow:hidden}
  .card--front{top:165px;background:var(--paper)}
  .card--back{top:653px;background:var(--charcoal)}

  .front-mark{position:absolute;left:348px;top:-35px;width:462px;height:462px}

  .brand-name{font-weight:800;text-transform:uppercase;line-height:1;letter-spacing:.5px}
  .card--front .brand-name{position:absolute;left:42px;top:45px;width:260px;font-size:27px;color:var(--ink)}

  .person{position:absolute;left:43px;top:146px}
  .person__name{font-weight:700;font-size:22px;color:var(--ink);text-transform:uppercase;letter-spacing:.3px;line-height:1}
  .person__role{font-size:16px;color:var(--orange);text-transform:uppercase;margin-top:5px;line-height:1}

  .address{position:absolute;left:43px;top:204px;font-size:16px;line-height:19.5px;color:var(--ink);font-style:normal}

  .contacts{position:absolute;left:43px;top:276px;list-style:none;font-size:16px;color:var(--ink)}
  .contacts li{display:flex;align-items:center;height:20px;line-height:20px}
  .contacts li.small{font-size:15px}
  .contacts svg{width:12px;height:12px;margin-right:9px;fill:var(--orange);flex:none}

  .card--back .brand-name{position:absolute;left:0;right:0;top:140px;text-align:center;font-size:36px;line-height:1;color:#f3f3f3}
  .back-url{position:absolute;left:0;right:0;top:323px;text-align:center;font-size:16px;font-weight:500;color:var(--orange)}
</style>
</head>
<body>
  <section class="card card--front">
    <svg class="front-mark" viewBox="0 0 462 462" aria-hidden="true"><circle cx="231" cy="231" r="231" fill="var(--charcoal)"/></svg>
    <div class="brand-name">Northfield<br>Builders<br>Guild</div>
    <div class="person">
      <div class="person__name">Daniel Hart</div>
      <div class="person__role">President</div>
    </div>
    <address class="address">
      2450 NE Alder Way,<br>Suite #210<br>Salem, OR 97301
    </address>
    <ul class="contacts">
      <li><svg viewBox="0 0 16 16"><path d="M3 1l3 3-1.5 2a9 9 0 0 0 5.5 5.5L12 10l3 3-2 2C7 15 1 9 1 3z"/></svg>(555) 214-7730</li>
      <li><svg viewBox="0 0 16 16"><path d="M4 0h8a1 1 0 0 1 1 1v14a1 1 0 0 1-1 1H4a1 1 0 0 1-1-1V1a1 1 0 0 1 1-1zm1 2v10h6V2z"/></svg>555.380.1946</li>
      <li class="small"><svg viewBox="0 0 16 16"><path d="M1 3h14v10H1zm1.5 1.5L8 9l5.5-4.5z"/></svg>hello@nbguild.org</li>
      <li class="small"><svg viewBox="0 0 16 16"><circle cx="8" cy="8" r="7"/></svg>builderslinkguild.org</li>
    </ul>
  </section>

  <section class="card card--back">
    <div class="brand-name">Northfield<br>Builders<br>Guild</div>
    <div class="back-url">www.builderslinkguild.org</div>
  </section>
</body>
</html>
```